Corinnehabbard.com

1. Conceptualization and designing of the site Homepage. The Homepage design will be completely customized and based on your design instructions (i.e. preferred colors, links to reference sites that you want us to take reference from if any etc) and the recently completed logo design.
2. Upon homepage design approval, based on it we will be creating the layout for the other 4 site inner pages (i.e. About page, Contact page, Services page, and Insights (publications, media).
3. Once all the inner page designs are approved, we will get the designs built (will make sure that the site is completely Responsive - works on all devices) within your provided WIX account.
4. We will add the static text and images provided by you to the Home page, About page, Contact page, and the Services page. For the 2 Insights sub-pages, we will add 1-2 sample Publications and Media entries.
once you confirm the total number of required entries for the 2 sub-pages, I will accordingly quote you on the same
5. Integration of a Contact form on the Contact page that will email the filled in details to your mail id.

```html
<!DOCTYPE html>
<html lang="en">
<head>
<meta charset="utf-8">
<title>Corinne Habbard Consulting</title>
<link href="https://fonts.googleapis.com/css2?family=Jost:wght@300;400;500;600;700;800&display=swap" rel="stylesheet">
<style>
:root{
  --blue:#0a8fd8;
  --blue-dark:#0a56b8;
  --orange:#f39200;
  --green:#1a9f4a;
  --red:#e3171b;
  --ink:#1b1b1b;
  --text:#4a4a4a;
  --grey:#f1f1f1;
  --footer:#111214;
}
*{margin:0;padding:0;box-sizing:border-box}
html,body{width:1200px;height:3783px;overflow:hidden}
body{font-family:"Jost",sans-serif;color:var(--ink);background:#fff;position:relative}
.abs{position:absolute}
.topline{top:0;left:0;width:1200px;height:5px;background:linear-gradient(90deg,var(--blue) 0 25%,var(--green) 25% 50%,var(--orange) 50% 75%,var(--red) 75%)}
/* header */
.brand{display:flex;align-items:center;gap:12px;color:var(--blue);font-weight:600;text-transform:uppercase;line-height:1.05}
.brand-dot{width:44px;height:44px;border-radius:50%;border:3px solid var(--blue);flex:none}
.brand-name{font-size:19px;letter-spacing:.5px}
.brand-sub{font-size:13px;letter-spacing:3px}
.contact{display:flex;align-items:center;gap:14px}
.contact .ic{width:38px;height:38px;border-radius:50%;border:1.5px solid #555;display:flex;align-items:center;justify-content:center}
.contact small{display:block;font-size:14px;text-transform:uppercase}
.contact b{font-size:18px;font-weight:500}
.nav{display:flex;gap:48px;font-size:15px;text-transform:uppercase}
.nav a{color:var(--ink);text-decoration:none;padding-bottom:6px}
.nav a.on{color:var(--blue);font-weight:600;border-bottom:2px solid var(--blue)}
/* hero */
.hero{top:163px;left:0;width:1200px;height:640px;background:linear-gradient(100deg,#5aa7cf 0%,#9fcde4 35%,#c8dfe8 55%,#6f8ea3 78%,#3a6a92 100%)}
.hero h1{color:#fff;font-weight:700;font-size:35px;line-height:45px;text-transform:uppercase;letter-spacing:.5px}
.field{background:#fff;font-size:12px;padding:14px 17px;text-transform:uppercase;color:#333}
.btn{background:var(--orange);color:#fff;font-weight:700;text-transform:uppercase;display:flex;align-items:center;justify-content:center}
/* sections */
.title{width:1200px;text-align:center;color:var(--blue);font-weight:700;font-size:31px;text-transform:uppercase;letter-spacing:.5px}
.dots{display:flex;gap:9px}
.dots i{width:10px;height:10px;border-radius:50%;display:block}
.dots i:nth-child(1){background:var(--blue)}.dots i:nth-child(2){background:var(--green)}.dots i:nth-child(3){background:var(--orange)}.dots i:nth-child(4){background:var(--red)}
.card{width:460px;height:275px;background:#fff;box-shadow:0 2px 14px rgba(0,0,0,.09)}
.card .icon{position:absolute;left:30px;top:50px;width:120px;height:120px;border-radius:50%;border:2px solid #222;display:flex;align-items:center;justify-content:center}
.card h3{position:absolute;left:180px;top:42px;width:260px;font-size:16px;font-weight:500;line-height:25px;text-transform:uppercase}
.card p{position:absolute;left:180px;top:100px;width:265px;font-size:12.5px;line-height:19px;color:var(--text)}
.card .btn{position:absolute;left:183px;top:200px;width:117px;height:34px;font-size:13px}
.about{top:1686px;left:0;width:1200px;height:518px;background:linear-gradient(120deg,#f3f3f3,#e7e7e7 50%,#f5f5f5)}
.about p{font-size:15.5px;line-height:22.5px;color:var(--text);font-weight:300}
.insight{top:2388px;left:133px;width:935px;height:475px;background:#fff;box-shadow:0 2px 18px rgba(0,0,0,.08)}
.insight p{font-size:15.5px;line-height:22.5px;color:var(--text);font-weight:300}
.cta{top:2981px;left:0;width:1200px;height:420px;background:var(--blue-dark)}
.footer{top:3300px;left:0;width:1200px;height:483px;background:var(--footer)}
.fnav{display:flex;gap:40px;color:#fff;font-size:15px;text-transform:uppercase;width:1200px;justify-content:center}
</style>
</head>
<body>
<div class="abs topline"></div>

<!-- header -->
<div class="abs brand" style="left:133px;top:48px">
  <span class="brand-dot"></span>
  <span><span class="brand-name">Corinne Habbard</span><br><span class="brand-sub">Consulting</span></span>
</div>
<div class="abs contact" style="left:527px;top:40px">
  <span class="ic"><svg width="18" height="14" viewBox="0 0 18 14"><rect x="1" y="1" width="16" height="12" fill="none" stroke="#333" stroke-width="1.4"/><path d="M1 1l8 7 8-7" fill="none" stroke="#333" stroke-width="1.4"/></svg></span>
  <span><small>Email us</small><b>info@corinnehabbard.com</b></span>
</div>
<div class="abs contact" style="left:862px;top:40px">
  <span class="ic"><svg width="18" height="18" viewBox="0 0 24 24"><path d="M6 3l3 4-2 2c1 3 4 6 7 7l2-2 4 3-2 4C10 21 3 14 3 5z" fill="none" stroke="#333" stroke-width="1.6"/></svg></span>
  <span><small>Call us</small><b>+1 555 010 0199</b></span>
</div>
<nav class="abs nav" style="left:527px;top:109px">
  <a class="on">Home</a><a>About us</a><a>Insights</a><a>Services</a><a>Contact us</a>
</nav>

<!-- hero -->
<div class="abs hero" role="img" aria-label="Smiling nurse in blue scrubs with arms crossed beside a laptop in a bright hospital office"></div>
<h1 class="abs" style="left:131px;top:205px;top:205px" >Nurses consult for<br>efficient &amp; empathetic<br>solutions.</h1>
<div class="abs field" style="left:134px;top:370px;width:248px;height:42px">First name</div>
<div class="abs field" style="left:397px;top:370px;width:248px;height:42px">Last name</div>
<div class="abs field" style="left:134px;top:426px;width:248px;height:42px">Email ID</div>
<div class="abs field" style="left:397px;top:426px;width:248px;height:42px">Phone</div>
<div class="abs field" style="left:134px;top:482px;width:514px;height:104px">Message</div>
<div class="abs btn" style="left:134px;top:609px;width:134px;height:51px;font-size:19px">Submit</div>

<svg class="abs" style="left:0;top:680px" width="1200" height="140" viewBox="0 0 1200 140">
  <polygon points="0,22 600,110 1200,22 1200,140 0,140" fill="#fff"/>
  <polygon points="0,12 600,97 600,113 0,30" fill="var(--blue)"/>
  <polygon points="1200,12 600,97 600,113 1200,30" fill="var(--orange)"/>
</svg>
<div class="abs" style="left:553px;top:737px;width:94px;height:94px;border-radius:50%;background:#fff;box-shadow:0 0 0 2px #ddd"></div>

<!-- services -->
<h2 class="abs title" style="top:853px">Our Services</h2>
<div class="abs dots" style="left:571px;top:920px"><i></i><i></i><i></i><i></i></div>

<div class="abs card" style="left:134px;top:1032px">
  <div class="icon"><svg width="64" height="64" viewBox="0 0 64 64" fill="none" stroke="#222" stroke-width="2.5"><circle cx="32" cy="32" r="18"/><path d="M32 6v8M32 50v8M6 32h8M50 32h8M13 13l6 6M45 45l6 6M13 51l6-6M45 19l6-6"/><circle cx="32" cy="32" r="9" fill="var(--orange)" stroke="none"/><path d="M32 27v10M27 32h10" stroke="#fff"/></svg></div>
  <h3>Healthcare optimization solutions</h3>
  <p>Lorem ipsum dolor sit amet, consectetur adipiscing elit, sed do eiusmod tempor incididunt ut labore et dolore magna aliqua. Ut enim ad minim veniam</p>
  <div class="btn">Read more</div>
</div>
<div class="abs card" style="left:611px;top:1032px">
  <div class="icon"><svg width="60" height="60" viewBox="0 0 60 60" fill="none" stroke="#222" stroke-width="2.5"><rect x="12" y="12" width="36" height="36" rx="4"/><path d="M30 20v20M20 30h20" stroke="var(--orange)" stroke-width="4"/></svg></div>
  <h3>Industry-specific nursing expertise</h3>
  <p>Lorem ipsum dolor sit amet, consectetur adipiscing elit, sed do eiusmod tempor incididunt ut labore et dolore magna aliqua. Ut enim ad minim veniam</p>
  <div class="btn">Read more</div>
</div>
<div class="abs card" style="left:134px;top:1327px">
  <div class="icon"><svg width="60" height="64" viewBox="0 0 60 64" fill="none" stroke="#222" stroke-width="2.5"><path d="M20 40c-6-5-8-10-8-16a18 18 0 0136 0c0 6-2 11-8 16v6H20z"/><path d="M22 52h16M24 58h12"/><circle cx="30" cy="25" r="7" fill="var(--orange)" stroke="none"/></svg></div>
  <h3>Cross-sector problem solving</h3>
  <p>Lorem ipsum dolor sit amet, consectetur adipiscing elit, sed do eiusmod tempor incididunt ut labore et dolore magna aliqua. Ut enim ad minim veniam</p>
  <div class="btn">Read more</div>
</div>
<div class="abs card" style="left:611px;top:1327px">
  <div class="icon"><svg width="60" height="64" viewBox="0 0 60 64" fill="none" stroke="#222" stroke-width="2.5"><path d="M40 60V46c6-4 10-10 10-18a20 20 0 00-40 0l-4 10 5 2v8a5 5 0 005 5h6v7"/><circle cx="30" cy="28" r="8" fill="var(--orange)" stroke="none"/><circle cx="30" cy="28" r="13"/></svg></div>
  <h3>Nursing-led consultation services</h3>
  <p>Lorem ipsum dolor sit amet, consectetur adipiscing elit, sed do eiusmod tempor incididunt ut labore et dolore magna aliqua. Ut enim ad minim veniam</p>
  <div class="btn">Read more</div>
</div>

<!-- about -->
<div class="abs about"></div>
<div class="abs" role="img" aria-label="Portrait of Corinne Habbard, consultant, smiling in a dark top" style="left:137px;top:1740px;width:463px;height:464px;background:linear-gradient(180deg,#c9c9c9,#7a6a60 55%,#2a2a2a)"></div>
<h2 class="abs" style="left:661px;top:1740px;color:var(--blue);font-size:31px;font-weight:700;text-transform:uppercase">About us</h2>
<div class="abs" style="left:912px;top:1745px;width:58px;height:58px;border-radius:50%;border:2px dotted #c9a24a;background:#fff"></div>
<div class="abs" style="left:1016px;top:1750px;width:50px;height:50px;background:#0d2a5c"></div>
<div class="abs dots" style="left:661px;top:1810px"><i></i><i></i><i></i><i></i></div>
<p class="abs" style="left:658px;top:1862px;width:412px;font-size:15.5px;line-height:22.5px;color:var(--text);font-weight:300">Sed ut perspiciatis unde omnis iste natus error sit volu ptatem accusantium doloremque laudantium, totam rem aperiam, eaque ipsa quae ab illo inventore veritatis et quasi architecto beatae vitae dicta sunt explicabo. Nemo enim ipsam voluptatem quia voluptas sit aspernatur aut odit aut fugit, sed quia consequuntur magni dolores eos qui ratione voluptatem sequi nesciunt. Neque porro quisquam est, qui dolorem ipsum quia dolor sit amet, consectetur, adipisci velit, sed quia non numquam eius modi tempora incidunt ut labore et dolore magnam aliquam</p>
<div class="abs btn" style="left:659px;top:2120px;width:117px;height:34px;font-size:13px">Read more</div>

<!-- insights -->
<h2 class="abs title" style="top:2256px">Insights</h2>
<div class="abs dots" style="left:569px;top:2322px"><i></i><i></i><i></i><i></i></div>
<svg class="abs" style="left:50px;top:2595px" width="30" height="50" viewBox="0 0 30 50"><path d="M26 2L4 25l22 23" fill="none" stroke="#aaa" stroke-width="2.5"/></svg>
<svg class="abs" style="left:1110px;top:2595px" width="30" height="50" viewBox="0 0 30 50"><path d="M4 2l22 23L4 48" fill="none" stroke="#aaa" stroke-width="2.5"/></svg>
<div class="abs insight">
  <div class="abs" style="left:52px;top:44px;font-size:16px;color:#333;font-weight:300">Published: Feb. 09, 2024, 8:30 a.m.</div>
  <h3 class="abs" style="left:53px;top:78px;width:380px;font-size:19px;line-height:29px;font-weight:500;text-transform:uppercase">A longtime Lakeshore Health nurse is now a National Leadership Scholar</h3>
  <p class="abs" style="left:53px;top:186px;width:370px">RIVERTON, MI - Many Lakeshore Health nurses have mentored Corinne Habbard throughout her 25-year career at the Riverton health system.</p>
  <p class="abs" style="left:53px;top:276px;width:370px">The longtime nurse and current clinical information analyst now has four "mentors" among the former national leadership fellows of the program.</p>
  <div class="abs btn" style="left:56px;top:385px;width:117px;height:34px;font-size:13px">Read more</div>
  <div class="abs" role="img" aria-label="Corinne Habbard standing before a carved wooden doorway between two flags" style="left:484px;top:0;width:451px;height:475px;background:linear-gradient(90deg,#c9bfb0,#6a3a22 30%,#4a2616 70%,#c6bcae)"></div>
</div>
<div class="abs" style="left:550px;top:2906px;display:flex;gap:11px">
  <i style="width:11px;height:11px;border-radius:50%;background:var(--orange)"></i>
  <i style="width:11px;height:11px;border-radius:50%;background:#bbb"></i>
  <i style="width:11px;height:11px;border-radius:50%;background:#bbb"></i>
  <i style="width:11px;height:11px;border-radius:50%;background:#bbb"></i>
  <i style="width:11px;height:11px;border-radius:50%;background:#bbb"></i>
</div>

<!-- call to action -->
<div class="abs cta"></div>
<h2 class="abs" style="top:3048px;width:1200px;text-align:center;color:#fff;font-weight:700;font-size:29px;line-height:45px;text-transform:uppercase">We diagnose &amp; solve challenges<br>across industries</h2>
<p class="abs" style="top:3160px;left:270px;width:660px;text-align:center;color:#e6eefb;font-size:16px;line-height:26px;font-weight:300">Sed ut perspiciatis unde omnis iste natus error sit voluptatem accusantium doloremque laudantium, totam rem aperiam, eaque ipsa quae ab illo inventore veritatis</p>
<div class="abs btn" style="left:511px;top:3246px;width:178px;height:50px;font-size:18px">Contact us</div>

<!-- footer -->
<div class="abs footer"></div>
<svg class="abs" style="left:0;top:3290px" width="1200" height="120" viewBox="0 0 1200 120">
  <polygon points="0,0 1200,0 1200,10 600,75 0,10" fill="var(--blue-dark)"/>
  <polygon points="0,0 600,65 600,82 0,17" fill="var(--blue)"/>
  <polygon points="1200,0 600,65 600,82 1200,17" fill="var(--orange)"/>
</svg>
<div class="abs" style="left:555px;top:3455px;width:90px;height:90px;border-radius:50%;border:3px solid var(--blue)"></div>
<div class="abs" style="top:3556px;width:1200px;text-align:center;color:var(--blue);font-weight:600;text-transform:uppercase;line-height:1.05">
  <div style="font-size:26px;letter-spacing:.5px">Corinne Habbard</div>
  <div style="font-size:18px;letter-spacing:5px">Consulting</div>
</div>
<nav class="abs fnav" style="top:3652px;gap:40px"><span>Home</span><span>About us</span><span>Insights</span><span>Services</span><span>Contact us</span></nav>
<div class="abs" style="top:3720px;width:1200px;text-align:center;color:#ddd;font-size:13px">Copyright © 2024 All Rights Reserved</div>
</body>
</html>
```